Tidewell Comforts, a portable luxury restroom trailer company needs a landing page

We need a landing page for a luxury portable restroom trailer company. This should be modern, and simple - use any combination of Pantone colors: Warm Gray 1C, Black 7C, 7529c, 873C, 8003C

We rent these trailers for special events like weddings, private parties, festivals, family reunions, team building, wine tastings, beer tastings, food truck round-ups, etc.

An idea of the landing page is in the files below. Please use stock photography and placeholder text for now. The winning design will be given final content.

Requirements
Must have
• Multiple "Get Quote" buttons or a place for them to type in type of rental, how many people etc

```html
<!DOCTYPE html>
<html lang="en">
<head>
<meta charset="utf-8">
<title>Tidewell Comforts – Luxury Portable Restroom Trailers</title>
<link href="https://fonts.googleapis.com/css2?family=Rubik:wght@400;500;600&family=IBM+Plex+Sans:wght@400;500;600&family=IBM+Plex+Serif:wght@400&display=swap" rel="stylesheet">
<style>
:root{
  --brand:#0b6bb6;
  --brand-dark:#0a5e9f;
  --ink:#1c1c1c;
  --text:#3a3a3a;
  --muted:#666;
  --hero-bg:#f1f0ef;
  --section-alt:#f2f2f2;
  --line:#dcdcdc;
  --white:#fff;
}
*{box-sizing:border-box;margin:0;padding:0}
html,body{width:1200px;height:2862px;overflow:hidden}
body{font-family:"IBM Plex Sans",sans-serif;color:var(--text);background:var(--white);position:relative}
.serif{font-family:"IBM Plex Serif",serif}

/* Header */
.site-header{height:78px;display:flex;align-items:center;padding:0 131px;justify-content:space-between}
.logo{font-family:"Rubik",sans-serif;font-weight:500;font-size:24px;color:var(--brand)}
.nav{display:flex;gap:58px}
.nav a{font-family:"Rubik",sans-serif;font-weight:500;font-size:15.5px;color:var(--ink);text-decoration:none;letter-spacing:.3px}

/* Hero */
.hero{position:relative;height:645px;background:var(--hero-bg)}
.photo{position:absolute;display:block}
.tag-label{position:absolute;font-size:12.5px;color:var(--ink);letter-spacing:.3px;white-space:nowrap}
.vertical{transform:rotate(-90deg);transform-origin:left top}
.hero-title{position:absolute;left:348px;top:484px;font-size:28px;line-height:32px;color:var(--ink);font-weight:400}
.btn{display:inline-block;background:var(--brand);color:var(--white);font-family:"Rubik",sans-serif;font-weight:500;text-decoration:none;text-align:center}
.hero .btn{position:absolute;left:349px;top:565px;width:101px;height:33px;line-height:33px;font-size:14px}

/* Events */
.events{height:491px;position:relative}
.section-title{font-family:"Rubik",sans-serif;font-weight:500;font-size:24px;color:var(--ink);letter-spacing:.3px}
.events .section-title{position:absolute;top:38px;left:131px}
.event-card{position:absolute;top:89px;width:299px;height:357px;border:1px solid var(--line);background:var(--white)}
.event-img{position:absolute;left:0;top:0;width:100%;height:156px}
.event-type{position:absolute;left:0;top:18px;background:var(--white);font-size:12px;padding:2px 5px;color:var(--text)}
.event-date{position:absolute;left:20px;top:136px;height:40px;display:flex;background:var(--brand-dark);color:var(--white)}
.event-date span{display:flex;flex-direction:column;justify-content:center;padding:0 8px}
.event-date span + span{border-left:1px solid rgba(255,255,255,.35)}
.event-date small{font-size:10px;line-height:11px}
.event-date b{font-family:"IBM Plex Serif",serif;font-weight:400;font-size:15px;line-height:18px}
.event-body{position:absolute;left:20px;right:14px;top:193px}
.event-body h3{font-family:"IBM Plex Serif",serif;font-weight:400;font-size:14.5px;line-height:19px;color:var(--ink)}
.event-body p{font-size:11.4px;line-height:17.5px;margin-top:14px;color:var(--text)}
.small-btn{height:23px;line-height:23px;font-size:10px;padding:0 10px}
.event-card .small-btn{position:absolute;left:21px;top:311px}

/* Products */
.products{height:964px;background:var(--section-alt);position:relative}
.products .section-title{position:absolute;top:40px;left:130px}
.product{position:absolute;left:131px;width:935px;height:262px;background:var(--white)}
.product-img{position:absolute;right:0;top:0;width:393px;height:262px}
.product-body{position:absolute;left:39px;top:33px;width:470px}
.product-tag{display:inline-block;border:1px solid var(--line);font-family:"IBM Plex Serif",serif;font-size:12px;padding:3px 11px}
.product-body h3{font-family:"IBM Plex Serif",serif;font-weight:400;font-size:19px;color:var(--ink);margin-top:18px;white-space:nowrap}
.product-body p{font-size:11.6px;line-height:17.7px;margin-top:6px;width:445px}
.product-body .small-btn{margin-top:20px;margin-left:2px}

/* Quote */
.quote{position:relative;height:525px}
.quote-bg{position:absolute;inset:0;width:100%;height:100%}
.quote h2{position:absolute;top:60px;width:100%;text-align:center;font-family:"Rubik",sans-serif;font-weight:500;font-size:28px;color:var(--white);letter-spacing:.3px}
.quote-form{position:absolute;left:134px;top:134px;width:933px;height:321px;background:#f4f4f4}
.field{position:absolute;width:282px;height:47px;border:1px solid #c9c9c9;background:var(--white);display:flex;align-items:center;justify-content:space-between;padding:0 13px;font-size:11px;font-weight:500;color:var(--ink);letter-spacing:.2px;white-space:nowrap}
.field svg{width:12px;height:12px;flex:none}
.col-1{left:25px}.col-2{left:323px}.col-3{left:622px}
.row-1{top:38px}.row-2{top:98px}.row-3{top:158px}
.submit{position:absolute;left:397px;top:230px;width:140px;height:53px;line-height:53px;font-size:20px;border:0}

/* Footer */
.site-footer{position:absolute;left:0;top:2703px;width:1200px;height:159px;background:var(--brand)}
.site-footer .bar{position:absolute;left:131px;right:133px;top:26px;display:flex;justify-content:space-between;align-items:center;height:40px}
.site-footer .logo,.site-footer .nav a{color:var(--white)}
.site-footer hr{position:absolute;left:131px;right:133px;top:82px;border:0;border-top:1px solid rgba(255,255,255,.25)}
.copyright{position:absolute;top:115px;width:100%;text-align:center;font-size:12px;color:var(--white)}
</style>
</head>
<body>

<header class="site-header">
  <div class="logo">Tidewell Comforts</div>
  <nav class="nav"><a href="#events">EVENT</a><a href="#products">PRODUCT</a><a href="#quote">CONTACT</a></nav>
</header>

<section class="hero">
  <svg class="photo" style="left:133px;top:20px;width:230px;height:308px" role="img" aria-label="Wedding couple under string lights at night"><defs><linearGradient id="g1" x1="0" y1="0" x2="0" y2="1"><stop offset="0" stop-color="#4d5a2a"/><stop offset="1" stop-color="#8a6a3e"/></linearGradient></defs><rect width="100%" height="100%" fill="url(#g1)"/></svg>
  <span class="tag-label vertical" style="left:116px;top:168px">WEDDINGS</span>

  <span class="tag-label" style="left:379px;top:37px">PRIVATE PARTIES</span>
  <svg class="photo" style="left:379px;top:56px;width:252px;height:169px" role="img" aria-label="Friends dancing outdoors beside a trailer"><defs><linearGradient id="g2" x1="0" y1="0" x2="1" y2="1"><stop offset="0" stop-color="#9aa49a"/><stop offset="1" stop-color="#5a6a3a"/></linearGradient></defs><rect width="100%" height="100%" fill="url(#g2)"/></svg>

  <span class="tag-label" style="left:650px;top:66px">FAMILY REUNIONS</span>
  <svg class="photo" style="left:607px;top:86px;width:296px;height:199px" role="img" aria-label="Family gathered around a dinner table"><defs><linearGradient id="g3" x1="0" y1="0" x2="1" y2="1"><stop offset="0" stop-color="#d8d4cc"/><stop offset="1" stop-color="#7a6048"/></linearGradient></defs><rect width="100%" height="100%" fill="url(#g3)"/></svg>

  <svg class="photo" style="left:859px;top:109px;width:208px;height:267px" role="img" aria-label="Group relaxing outside a camper trailer"><defs><linearGradient id="g4" x1="0" y1="0" x2="0" y2="1"><stop offset="0" stop-color="#dcdcdc"/><stop offset="1" stop-color="#6a7a62"/></linearGradient></defs><rect width="100%" height="100%" fill="url(#g4)"/></svg>
  <span class="tag-label" style="left:860px;top:383px">BEER TASTINGS</span>

  <svg class="photo" style="left:324px;top:239px;width:307px;height:205px" role="img" aria-label="Festival crowd under fireworks"><defs><linearGradient id="g5" x1="0" y1="0" x2="0" y2="1"><stop offset="0" stop-color="#3a2434"/><stop offset="1" stop-color="#a0623a"/></linearGradient></defs><rect width="100%" height="100%" fill="url(#g5)"/></svg>
  <span class="tag-label" style="left:322px;top:448px">FESTIVALS</span>

  <svg class="photo" style="left:137px;top:341px;width:175px;height:259px" role="img" aria-label="Hand holding a glass of red wine at sunset"><defs><linearGradient id="g6" x1="0" y1="0" x2="1" y2="1"><stop offset="0" stop-color="#b79a6a"/><stop offset="1" stop-color="#4c4a2a"/></linearGradient></defs><rect width="100%" height="100%" fill="url(#g6)"/></svg>
  <span class="tag-label" style="left:137px;top:605px">WINE TASTINGS</span>

  <svg class="photo" style="left:643px;top:294px;width:205px;height:202px" role="img" aria-label="Teal food truck parked on a street"><defs><linearGradient id="g7" x1="0" y1="0" x2="0" y2="1"><stop offset="0" stop-color="#8a9a94"/><stop offset="1" stop-color="#2aa3a6"/></linearGradient></defs><rect width="100%" height="100%" fill="url(#g7)"/></svg>
  <span class="tag-label" style="left:642px;top:507px">FOOD TRUCK ROUND-UPS</span>

  <svg class="photo" style="left:812px;top:439px;width:255px;height:187px" role="img" aria-label="Colleagues giving a group high five"><defs><linearGradient id="g8" x1="0" y1="0" x2="1" y2="0"><stop offset="0" stop-color="#8e8e8c"/><stop offset="1" stop-color="#c8cfd4"/></linearGradient></defs><rect width="100%" height="100%" fill="url(#g8)"/></svg>
  <span class="tag-label vertical" style="left:1074px;top:627px">TEAM BUILDING</span>

  <h1 class="hero-title serif">Luxury Portable<br>Restroom Trailer</h1>
  <a class="btn" href="#products">READ MORE</a>
</section>

<section class="events" id="events">
  <h2 class="section-title">EVENTS</h2>

  <article class="event-card" style="left:132px">
    <svg class="event-img" role="img" aria-label="Couple celebrating at an outdoor wedding table"><defs><linearGradient id="e1" x1="0" y1="0" x2="1" y2="1"><stop offset="0" stop-color="#7a8060"/><stop offset="1" stop-color="#a87a4a"/></linearGradient></defs><rect width="100%" height="100%" fill="url(#e1)"/></svg>
    <span class="event-type">Wedding</span>
    <div class="event-date"><span><small>Monday</small><b>31 Jan 2022</b></span><span><small>AM</small><b>11:00</b></span></div>
    <div class="event-body"><h3>Lorem Ipsum is simply dummy text<br>of the printing and</h3><p>There are many variations of passages of<br>Lorem Ipsum available, but the majority have<br>suffered alteration in some form.</p></div>
    <a class="btn small-btn" href="#">READ MORE</a>
  </article>

  <article class="event-card" style="left:450px">
    <svg class="event-img" role="img" aria-label="Red festival trailer in an open lot"><defs><linearGradient id="e2" x1="0" y1="0" x2="0" y2="1"><stop offset="0" stop-color="#d4d8dc"/><stop offset=".45" stop-color="#c8262a"/><stop offset="1" stop-color="#8a8a80"/></linearGradient></defs><rect width="100%" height="100%" fill="url(#e2)"/></svg>
    <span class="event-type">Festival</span>
    <div class="event-date"><span><small>Tuesday</small><b>01 Feb 2022</b></span><span><small>AM</small><b>11:00</b></span></div>
    <div class="event-body"><h3>Lorem Ipsum is simply dummy text<br>of the printing and</h3><p>There are many variations of passages of<br>Lorem Ipsum available, but the majority have<br>suffered alteration in some form.</p></div>
    <a class="btn small-btn" href="#">READ MORE</a>
  </article>

  <article class="event-card" style="left:767px">
    <svg class="event-img" role="img" aria-label="Garden wine tasting hut among willow trees"><defs><linearGradient id="e3" x1="0" y1="0" x2="1" y2="0"><stop offset="0" stop-color="#6a7a3a"/><stop offset="1" stop-color="#2a2a2a"/></linearGradient></defs><rect width="100%" height="100%" fill="url(#e3)"/></svg>
    <span class="event-type">Wine Tasting</span>
    <div class="event-date"><span><small>Monday</small><b>21 Mar 2022</b></span><span><small>AM</small><b>11:00</b></span></div>
    <div class="event-body"><h3>Lorem Ipsum is simply dummy text<br>of the printing and</h3><p>There are many variations of passages of<br>Lorem Ipsum available, but the majority have<br>suffered alteration in some form.</p></div>
    <a class="btn small-btn" href="#">READ MORE</a>
  </article>
</section>

<section class="products" id="products">
  <h2 class="section-title">PRODUCTS</h2>

  <article class="product" style="top:95px">
    <div class="product-body">
      <span class="product-tag">Product 1</span>
      <h3>Lorem Ipsum is simply dummy text of the printing</h3>
      <p>There are many variations of passages of Lorem Ipsum available, but the majority have suffered alteration in some form, by injected humour, or randomised words which don't look even slightly believable. If you are going to use a passage of Lorem Ipsum, you need to be sure there isn't anything embarrassing.</p>
      <a class="btn small-btn" href="#">READ MORE</a>
    </div>
    <svg class="product-img" role="img" aria-label="Single restroom trailer with metal steps"><defs><linearGradient id="p1" x1="0" y1="0" x2="0" y2="1"><stop offset="0" stop-color="#6f8fb8"/><stop offset=".5" stop-color="#a7a496"/><stop offset="1" stop-color="#7a6a52"/></linearGradient></defs><rect width="100%" height="100%" fill="url(#p1)"/></svg>
  </article>

  <article class="product" style="top:373px">
    <div class="product-body">
      <span class="product-tag">Product 2</span>
      <h3>Lorem Ipsum is simply dummy text of the printing</h3>
      <p>There are many variations of passages of Lorem Ipsum available, but the majority have suffered alteration in some form, by injected humour, or randomised words which don't look even slightly believable. If you are going to use a passage of Lorem Ipsum, you need to be sure there isn't anything embarrassing.</p>
      <a class="btn small-btn" href="#">READ MORE</a>
    </div>
    <svg class="product-img" role="img" aria-label="Restroom trailer at a construction site"><defs><linearGradient id="p2" x1="0" y1="0" x2="0" y2="1"><stop offset="0" stop-color="#8fb6d8"/><stop offset=".4" stop-color="#b88a5a"/><stop offset=".75" stop-color="#d8d8d4"/><stop offset="1" stop-color="#a08a6a"/></linearGradient></defs><rect width="100%" height="100%" fill="url(#p2)"/></svg>
  </article>

  <article class="product" style="top:653px">
    <div class="product-body">
      <span class="product-tag">Product 3</span>
      <h3>Lorem Ipsum is simply dummy text of the printing</h3>
      <p>There are many variations of passages of Lorem Ipsum available, but the majority have suffered alteration in some form, by injected humour, or randomised words which don't look even slightly believable. If you are going to use a passage of Lorem Ipsum, you need to be sure there isn't anything embarrassing.</p>
      <a class="btn small-btn" href="#">READ MORE</a>
    </div>
    <svg class="product-img" role="img" aria-label="White multi-stall restroom trailer among trees"><defs><linearGradient id="p3" x1="0" y1="0" x2="0" y2="1"><stop offset="0" stop-color="#4a6a3a"/><stop offset=".45" stop-color="#e8eaec"/><stop offset="1" stop-color="#3a3e40"/></linearGradient></defs><rect width="100%" height="100%" fill="url(#p3)"/></svg>
  </article>
</section>

<section class="quote" id="quote">
  <svg class="quote-bg" role="img" aria-label="Restroom trailer among trees, darkened backdrop"><defs><linearGradient id="q" x1="0" y1="0" x2="0" y2="1"><stop offset="0" stop-color="#2c3a2c"/><stop offset=".5" stop-color="#4a4e4c"/><stop offset="1" stop-color="#222624"/></linearGradient></defs><rect width="100%" height="100%" fill="url(#q)"/></svg>
  <h2>CONTACT US FOR A QUOTE</h2>
  <form class="quote-form">
    <div class="field col-1 row-1">NAME</div>
    <div class="field col-2 row-1">E MAIL</div>
    <div class="field col-3 row-1">PHONE</div>

    <div class="field col-1 row-2">TYPE OF EVENT?<svg viewBox="0 0 12 12"><path d="M2 4l4 4 4-4" fill="none" stroke="#222" stroke-width="1.5"/></svg></div>
    <div class="field col-2 row-2">HOW MANY PEOPLE?<svg viewBox="0 0 12 12"><path d="M2 4l4 4 4-4" fill="none" stroke="#222" stroke-width="1.5"/></svg></div>
    <div class="field col-3 row-2">TYPE OF PRODUCT YOU ARE INTERESTED IN?<svg viewBox="0 0 12 12"><path d="M2 4l4 4 4-4" fill="none" stroke="#222" stroke-width="1.5"/></svg></div>

    <div class="field col-1 row-3">WHEN DO YOU NEED IT?<svg viewBox="0 0 12 12"><rect x="1.5" y="2.5" width="9" height="8" fill="none" stroke="#222"/><path d="M1.5 5h9M4 1v3M8 1v3" stroke="#222"/></svg></div>
    <div class="field col-2 row-3">FOR HOW LONG?<svg viewBox="0 0 12 12"><circle cx="6" cy="6" r="4.5" fill="none" stroke="#222"/><path d="M6 3.5V6h2" fill="none" stroke="#222"/></svg></div>
    <div class="field col-3 row-3">WHERE?<svg viewBox="0 0 12 12"><path d="M6 11s3.5-4 3.5-6.3A3.5 3.5 0 0 0 2.5 4.7C2.5 7 6 11 6 11z" fill="#222"/><circle cx="6" cy="4.8" r="1.3" fill="#fff"/></svg></div>

    <button class="btn submit" type="submit">SUBMIT</button>
  </form>
</section>

<footer class="site-footer">
  <div class="bar">
    <div class="logo">Tidewell Comforts</div>
    <nav class="nav"><a href="#events">EVENT</a><a href="#products">PRODUCT</a><a href="#quote">CONTACT</a></nav>
  </div>
  <hr>
  <p class="copyright">Copyright © 2022 All Rights Reserved</p>
</footer>

</body>
</html>
```